Design a Travel and Tourism website

We would like a freelancer to design a website that is essentially easy to use and navigate database providing local information for Travelers about destination countries.

We proposed website would discuss different rates, fees, visa requirement, resort locations, cheap flights, etc. This website should be elegant and modern. Our business name is rovanix.
Some reference websites are zemplorift.ca, brindlefoxhaven.com,
There should be a forum in the website where travell\ers discuss about their first hand tranvel experience to such destinations.

Tourism

```html
<!DOCTYPE html>
<html lang="en">
<head>
<meta charset="utf-8">
<title>Rovanix — Travel and Tourism</title>
<link href="https://fonts.googleapis.com/css2?family=Roboto:wght@300;400;500;700&family=Roboto+Condensed:wght@400;700&display=swap" rel="stylesheet">
<style>
:root{
  --blue:#1f7fc1;
  --blue-dark:#17669e;
  --btn:#1a86c8;
  --orange:#f07c1d;
  --ink:#222;
  --text:#555;
  --muted:#888;
  --line:#e3e3e3;
  --light:#f4f4f4;
  --footer:#1f2330;
  --footer-bottom:#181b25;
  --white:#fff;
}
*{box-sizing:border-box;margin:0;padding:0}
html,body{width:1200px;height:3087px;overflow:hidden}
body{font-family:"Roboto",Arial,sans-serif;color:var(--text);background:var(--white);position:relative}
.abs{position:absolute}
a{color:inherit;text-decoration:none}
ul{list-style:none}

/* top bar */
.topbar{left:0;top:0;width:1200px;height:35px;background:var(--blue);color:var(--white);font-size:12px}
.topbar .contact{left:99px;top:0;height:35px;display:flex;align-items:center;gap:40px}
.topbar .contact span,.topbar .utils span{display:flex;align-items:center;gap:8px}
.topbar .utils{right:99px;top:0;height:35px;display:flex;align-items:center;gap:34px}

/* header */
.header{left:0;top:35px;width:1200px;height:95px;background:var(--white);border-bottom:3px solid #2a2f3a}
.brand{left:99px;top:22px;display:flex;align-items:center;gap:10px;font-size:34px;font-weight:500;color:var(--blue)}
.brand i{width:36px;height:36px;border-radius:50%;background:var(--blue);display:block}
.nav{right:99px;top:30px;display:flex;gap:0;font-family:"Roboto Condensed",sans-serif;font-size:13px;color:#333}
.nav a{padding:8px 12px;text-transform:uppercase}
.nav a.active{border:1px solid var(--blue);color:var(--blue)}

/* hero */
.hero{left:0;top:130px;width:1200px;height:617px;background:linear-gradient(180deg,#6f8394 0%,#8f9aa2 40%,#5b5f58 75%,#3c3d35 100%)}
.hero .foliage{left:0;top:0;width:330px;height:617px;background:linear-gradient(90deg,rgba(140,100,30,.7),rgba(120,90,40,0))}
.hero h1{left:0;top:180px;width:1200px;text-align:center;color:var(--white);font-size:40px;font-weight:700;line-height:50px;letter-spacing:.5px;text-shadow:0 2px 4px rgba(0,0,0,.3)}
.arrow{top:252px;width:34px;height:34px;border-radius:50%;background:rgba(0,0,0,.35);display:flex;align-items:center;justify-content:center}
.tabs{left:99px;top:364px;display:flex;gap:4px}
.tabs span{height:36px;padding:0 14px;background:var(--blue);color:var(--white);font-family:"Roboto Condensed",sans-serif;font-size:13px;display:flex;align-items:center;gap:6px;text-transform:uppercase}
.tabs span.on{background:#e9ecef;color:var(--blue)}
.search{left:99px;top:400px;width:1002px;height:186px;background:rgba(236,239,242,.92);padding:22px 26px}
.search label{position:absolute;font-size:11px;font-weight:700;color:#333;text-transform:uppercase}
.field{position:absolute;height:34px;background:var(--white);border:1px solid #d5d5d5;font-size:11px;color:#999;display:flex;align-items:center;padding:0 10px;justify-content:space-between}
.btn{background:var(--btn);color:var(--white);font-size:12px;font-weight:500;display:flex;align-items:center;justify-content:center;text-transform:uppercase}
.radio{position:absolute;font-size:12px;color:#444;display:flex;align-items:center;gap:6px}
.radio i{width:13px;height:13px;border-radius:50%;border:1px solid #999;background:#fff;display:block}

/* section titles */
.title{font-size:30px;color:var(--ink);text-transform:uppercase;font-weight:400}

/* deals */
.dots{right:99px;top:830px;display:flex;gap:5px}
.dots i{width:12px;height:12px;border-radius:50%;border:1px solid #bbb;display:block}
.dots i.on{background:var(--blue);border-color:var(--blue)}
.deal{top:901px;width:237px;height:313px;background:var(--white);box-shadow:0 1px 4px rgba(0,0,0,.15)}
.deal .photo{width:237px;height:196px;position:relative}
.deal .photo b{position:absolute;left:11px;bottom:12px;color:var(--white);font-size:15px;font-weight:500;text-transform:uppercase}
.deal .meta{height:46px;display:flex;align-items:center;justify-content:space-between;padding:0 11px;border-bottom:1px solid var(--line)}
.stars{display:flex;gap:2px}
.deal .btn{width:82px;height:26px;font-size:11px}
.deal p{padding:14px 11px;font-size:11px;line-height:18px;color:#666}

/* trip planning */
.planning{left:0;top:1309px;width:1200px;height:502px;background:linear-gradient(180deg,#2c6fb8 0%,#3a84c6 55%,#2f8fc0 100%)}
.planning .title{position:absolute;left:0;top:72px;width:1200px;text-align:center;color:var(--white)}
.plan{top:187px;width:310px;height:233px;background:var(--white);text-align:center;padding-top:66px}
.plan h3{font-size:20px;font-weight:400;color:#333;margin-bottom:12px}
.plan p{font-size:11px;line-height:20px;color:#777;padding:0 16px}
.plan .more{display:inline-block;margin-top:16px;padding-top:8px;border-top:1px solid #555;width:82px;font-size:12px;color:#444;text-transform:uppercase}
.diamond{top:-44px;left:113px;width:84px;height:84px}

/* packages */
.video{left:99px;top:1984px;width:479px;height:300px;background:linear-gradient(160deg,#7a8f9a 0%,#a49b84 50%,#6c5a40 100%)}
.video .cap{position:absolute;left:14px;top:12px;color:#fff;font-size:12px}
.video .play{position:absolute;left:209px;top:120px;width:60px;height:60px;border-radius:50%;border:2px solid #fff;background:rgba(0,0,0,.3);display:flex;align-items:center;justify-content:center;padding-left:4px}
.pkg{left:619px;width:480px;height:132px}
.pkg .thumb{position:absolute;left:0;top:0;width:174px;height:132px}
.pkg h4{position:absolute;left:196px;top:0;font-size:17px;font-weight:400;color:#444}
.pkg .price{position:absolute;left:196px;top:36px;font-size:15px;color:var(--orange);font-style:italic;font-weight:500}
.pkg p{position:absolute;left:196px;top:66px;width:284px;font-size:12px;line-height:19px;color:#777}

/* destinations */
.dest{left:0;top:2391px;width:1200px;height:342px;background:var(--light)}
.dest .title{position:absolute;left:0;top:70px;width:1200px;text-align:center;font-size:29px;color:#333}
.col{top:157px;font-size:12px;color:#555;line-height:25.5px}
.col li{padding-left:18px;position:relative}
.col li::before{content:"";position:absolute;left:2px;top:9px;border-left:5px solid #444;border-top:4px solid transparent;border-bottom:4px solid transparent}

/* footer */
.footer{left:0;top:2733px;width:1200px;height:292px;background:var(--footer);color:#ddd}
.footer .brand{left:99px;top:42px;color:var(--blue);font-size:32px}
.finfo{left:99px;top:110px;font-size:13px;color:#ddd;line-height:18px}
.finfo div{display:flex;gap:12px;margin-bottom:14px}
.fcol{top:50px;font-size:12px;color:#eee}
.fcol h5{font-size:16px;color:var(--orange);font-weight:500;text-transform:uppercase;margin-bottom:16px}
.fcol li{padding-left:16px;position:relative;line-height:24px}
.fcol li::before{content:"";position:absolute;left:0;top:8px;border-left:5px solid #ddd;border-top:4px solid transparent;border-bottom:4px solid transparent}
.news{left:860px;top:50px;width:241px}
.news h5{font-size:16px;color:var(--orange);font-weight:500;text-transform:uppercase;margin-bottom:16px}
.news p{font-size:12px;line-height:18px;color:#eee;margin-bottom:18px}
.news .input{height:40px;border:1px solid #bbb;font-size:12px;color:#eee;display:flex;align-items:center;padding:0 14px;margin-bottom:12px}
.news .btn{width:94px;height:38px}
.bottom{left:0;top:3025px;width:1200px;height:62px;background:var(--footer-bottom);color:#ccc;font-size:12px}
.bottom .copy{left:99px;top:23px}
.bottom .links{right:99px;top:23px;display:flex;gap:38px}
</style>
</head>
<body>

<div class="abs topbar">
  <div class="abs contact">
    <span><svg width="12" height="12" viewBox="0 0 24 24"><path fill="#fff" d="M6.6 10.8a15 15 0 006.6 6.6l2.2-2.2c.3-.3.7-.4 1-.2 1.1.4 2.3.6 3.6.6.6 0 1 .4 1 1V20c0 .6-.4 1-1 1A17 17 0 013 4c0-.6.4-1 1-1h3.5c.6 0 1 .4 1 1 0 1.3.2 2.5.6 3.6.1.3 0 .7-.2 1z"/></svg>+900 0412 7736</span>
    <span><svg width="13" height="11" viewBox="0 0 24 18"><rect x="1" y="1" width="22" height="16" fill="none" stroke="#fff" stroke-width="2"/><path d="M1 1l11 9 11-9" fill="none" stroke="#fff" stroke-width="2"/></svg>enquiries@rovanix.com.au</span>
  </div>
  <div class="abs utils">
    <span>LOG IN / REGISTER</span>
    <span>USD ($) <svg width="8" height="5"><path d="M0 0h8L4 5z" fill="#fff"/></svg></span>
    <span>ENGLISH <svg width="8" height="5"><path d="M0 0h8L4 5z" fill="#fff"/></svg></span>
  </div>
</div>

<header class="abs header">
  <div class="abs brand"><i></i>Rovanix</div>
  <nav class="abs nav">
    <a class="active">Home</a><a>About us</a><a>Holidays</a><a>Flights</a><a>Hotels</a><a>Car hire</a><a>Travel insurance</a><a>Contact</a>
  </nav>
</header>

<section class="abs hero" role="img" aria-label="Photograph of a tall iron tower over a city with autumn leaves in the foreground">
  <div class="abs foliage"></div>
  <h1 class="abs">TRAVELERS ABOUT<br>DESTINATION COUNTRIES</h1>
  <div class="abs arrow" style="left:36px"><svg width="10" height="12"><path d="M8 0L1 6l7 6" fill="none" stroke="#fff" stroke-width="2"/></svg></div>
  <div class="abs arrow" style="right:36px"><svg width="10" height="12"><path d="M2 0l7 6-7 6" fill="none" stroke="#fff" stroke-width="2"/></svg></div>
  <div class="abs tabs">
    <span>Hotels</span><span class="on">Flights</span><span>Car hire</span><span>Extras</span><span>Vacation</span>
  </div>
  <div class="abs search">
    <label style="left:26px;top:28px">Flying from</label>
    <div class="field" style="left:26px;top:48px;width:245px">City or airport <svg width="9" height="12" viewBox="0 0 12 16"><path d="M6 0a6 6 0 00-6 6c0 4.5 6 10 6 10s6-5.5 6-10a6 6 0 00-6-6zm0 8.5A2.5 2.5 0 116 3.5a2.5 2.5 0 010 5z" fill="#777"/></svg></div>
    <label style="left:292px;top:28px">Flying to</label>
    <div class="field" style="left:292px;top:48px;width:245px">City or airport <svg width="9" height="12" viewBox="0 0 12 16"><path d="M6 0a6 6 0 00-6 6c0 4.5 6 10 6 10s6-5.5 6-10a6 6 0 00-6-6zm0 8.5A2.5 2.5 0 116 3.5a2.5 2.5 0 010 5z" fill="#777"/></svg></div>
    <label style="left:560px;top:28px">Adults (18+)</label>
    <div class="field" style="left:560px;top:48px;width:170px;color:#444">1 <span>⇕</span></div>
    <label style="left:754px;top:28px">Children (0-17)</label>
    <div class="field" style="left:754px;top:48px;width:170px;color:#444">0 <span>⇕</span></div>
    <label style="left:26px;top:100px">Departing</label>
    <div class="field" style="left:26px;top:120px;width:245px">mm/dd/yyyy <svg width="11" height="11"><rect x=".5" y="1.5" width="10" height="9" fill="none" stroke="#777"/><path d="M0 4h11" stroke="#777"/></svg></div>
    <label style="left:292px;top:100px">Returning</label>
    <div class="field" style="left:292px;top:120px;width:245px">mm/dd/yyyy <svg width="11" height="11"><rect x=".5" y="1.5" width="10" height="9" fill="none" stroke="#777"/><path d="M0 4h11" stroke="#777"/></svg></div>
    <div class="radio" style="left:562px;top:130px"><i></i>Add a hotel</div>
    <div class="radio" style="left:657px;top:130px"><i></i>Add a car</div>
    <div class="btn" style="position:absolute;left:757px;top:120px;width:170px;height:36px">Booking now</div>
  </div>
</section>

<h2 class="abs title" style="left:99px;top:818px">Today's top deals</h2>
<div class="abs dots"><i class="on"></i><i></i><i></i><i></i></div>

<article class="abs deal" style="left:99px">
  <div class="photo" role="img" aria-label="Photograph of a hotel bedroom" style="background:linear-gradient(160deg,#5b3d4a,#2f2228 60%,#c9b9a8)"><b>Paris hotels</b></div>
  <div class="meta"><div class="stars"><svg width="60" height="10"><g fill="#f2a516"><circle cx="5" cy="5" r="4"/><circle cx="17" cy="5" r="4"/><circle cx="29" cy="5" r="4"/></g><g fill="none" stroke="#bbb"><circle cx="41" cy="5" r="3.5"/><circle cx="53" cy="5" r="3.5"/></g></svg></div><span class="btn">View deals</span></div>
  <p>Lorem ipsum dolor sit amet, consectetur adipisicing elit, sed do eiusmod</p>
</article>
<article class="abs deal" style="left:354px">
  <div class="photo" role="img" aria-label="Photograph of a city skyline and bridge at dusk" style="background:linear-gradient(180deg,#e6b06a,#7d6f78 55%,#2d3a4d)"><b>New York flights</b></div>
  <div class="meta"><div class="stars"><svg width="60" height="10"><g fill="#f2a516"><circle cx="5" cy="5" r="4"/><circle cx="17" cy="5" r="4"/><circle cx="29" cy="5" r="4"/></g><g fill="none" stroke="#bbb"><circle cx="41" cy="5" r="3.5"/><circle cx="53" cy="5" r="3.5"/></g></svg></div><span class="btn">View deals</span></div>
  <p>Lorem ipsum dolor sit amet, consectetur adipisicing elit, sed do eiusmod</p>
</article>
<article class="abs deal" style="left:609px">
  <div class="photo" role="img" aria-label="Photograph of a beach umbrella with city towers at sunset" style="background:linear-gradient(180deg,#5d7fa6,#e9a24c 55%,#b86a2c)"><b>Dubai holidays</b></div>
  <div class="meta"><div class="stars"><svg width="60" height="10"><g fill="#f2a516"><circle cx="5" cy="5" r="4"/><circle cx="17" cy="5" r="4"/><circle cx="29" cy="5" r="4"/></g><g fill="none" stroke="#bbb"><circle cx="41" cy="5" r="3.5"/><circle cx="53" cy="5" r="3.5"/></g></svg></div><span class="btn">View deals</span></div>
  <p>Lorem ipsum dolor sit amet, consectetur adipisicing elit, sed do eiusmod</p>
</article>
<article class="abs deal" style="left:864px">
  <div class="photo" role="img" aria-label="Photograph of people fishing from a lakeside jetty" style="background:linear-gradient(180deg,#8aa4a8,#5f7a5a 55%,#3d4a36)"><b>Benidorm holidays</b></div>
  <div class="meta"><div class="stars"><svg width="60" height="10"><g fill="#f2a516"><circle cx="5" cy="5" r="4"/><circle cx="17" cy="5" r="4"/><circle cx="29" cy="5" r="4"/></g><g fill="none" stroke="#bbb"><circle cx="41" cy="5" r="3.5"/><circle cx="53" cy="5" r="3.5"/></g></svg></div><span class="btn">View deals</span></div>
  <p>Lorem ipsum dolor sit amet, consectetur adipisicing elit, sed do eiusmod</p>
</article>

<section class="abs planning" role="img" aria-label="Background photograph of a tropical beach with palm trees">
  <h2 class="title">Trip planning</h2>
  <div class="abs plan" style="left:99px">
    <svg class="abs diamond" viewBox="0 0 84 84"><rect x="14" y="14" width="56" height="56" transform="rotate(45 42 42)" fill="#f07c1d"/><path d="M30 48h24M34 48l8-14 8 14M42 34v-4" stroke="#fff" stroke-width="3" fill="none"/></svg>
    <h3>Travel Deals</h3>
    <p>Nemo enim ipsam voluptatem quia voluptas sit aspernatur aut odit aut fugit, sed quia consequuntur magni dolores eos qui ratione voluptatem</p>
    <span class="more">Learn more</span>
  </div>
  <div class="abs plan" style="left:445px">
    <svg class="abs diamond" viewBox="0 0 84 84"><rect x="14" y="14" width="56" height="56" transform="rotate(45 42 42)" fill="#f07c1d"/><rect x="30" y="36" width="24" height="12" fill="none" stroke="#fff" stroke-width="3"/><path d="M30 50v4M54 50v4" stroke="#fff" stroke-width="3"/></svg>
    <h3>Top Hotel Destinations</h3>
    <p>Nemo enim ipsam voluptatem quia voluptas sit aspernatur aut odit aut fugit, sed quia consequuntur magni dolores eos qui ratione voluptatem</p>
    <span class="more">Learn more</span>
  </div>
  <div class="abs plan" style="left:791px">
    <svg class="abs diamond" viewBox="0 0 84 84"><rect x="14" y="14" width="56" height="56" transform="rotate(45 42 42)" fill="#f07c1d"/><path d="M30 50v-8l4-8h16l4 8v8z" fill="#fff"/><circle cx="35" cy="50" r="3" fill="#f07c1d"/><circle cx="49" cy="50" r="3" fill="#f07c1d"/></svg>
    <h3>Top Rental Car Destinations</h3>
    <p>Nemo enim ipsam voluptatem quia voluptas sit aspernatur aut odit aut fugit, sed quia consequuntur magni dolores eos qui ratione voluptatem</p>
    <span class="more">Learn more</span>
  </div>
</section>

<h2 class="abs title" style="left:0;top:1890px;width:1200px;text-align:center;color:#333">Popular vacation packages</h2>

<div class="abs video" role="img" aria-label="Video still of a family fishing on a wooden jetty">
  <span class="cap">Live your adventure</span>
  <svg style="position:absolute;right:14px;top:12px" width="12" height="12" viewBox="0 0 12 12"><circle cx="9" cy="2" r="2" fill="#fff"/><circle cx="3" cy="6" r="2" fill="#fff"/><circle cx="9" cy="10" r="2" fill="#fff"/><path d="M9 2L3 6l6 4" stroke="#fff" fill="none"/></svg>
  <div class="play"><svg width="18" height="20"><path d="M0 0l18 10-18 10z" fill="#fff"/></svg></div>
</div>

<div class="abs pkg" style="top:1984px">
  <div class="thumb" role="img" aria-label="Photograph of a beach umbrella near city towers" style="background:linear-gradient(180deg,#4f83b6,#c89c6b 60%,#b77d45)"></div>
  <h4>Nulla at diam ornare, aliquam</h4>
  <div class="price">$20.00, MAY 25, 2017</div>
  <p>Sed ut perspiciatis unde omnis iste natus error sit luptatem accusantium doloremque laudantium, totam rem aperiam, eaque ipsa quae</p>
</div>
<div class="abs pkg" style="top:2149px">
  <div class="thumb" role="img" aria-label="Photograph of friends at the beach" style="background:linear-gradient(160deg,#a9c6d6,#d8b58e 55%,#8f7a66)"></div>
  <h4>Nulla at diam ornare, aliquam</h4>
  <div class="price">$20.00, MAY 25, 2017</div>
  <p>Sed ut perspiciatis unde omnis iste natus error sit luptatem accusantium doloremque laudantium, totam rem aperiam, eaque ipsa quae</p>
</div>

<section class="abs dest">
  <h2 class="title">Travelers about destination countries</h2>
  <ul class="abs col" style="left:99px"><li>Algarve holidays</li><li>Alicante car hire</li><li>Amsterdam flights</li><li>Bangkok flights</li><li>Benidorm holidays</li></ul>
  <ul class="abs col" style="left:321px"><li>Blackpool hotels</li><li>Cuba holidays</li><li>Cyprus holidays</li><li>Dubai holidays</li><li>Dubai hotels</li></ul>
  <ul class="abs col" style="left:527px"><li>Faro car hire</li><li>Gran Canaria holidays</li><li>Lanzarote holidays</li><li>Las Vegas holidays</li><li>London hotels</li></ul>
  <ul class="abs col" style="left:753px"><li>Majorca car hire</li><li>Majorca holidays</li><li>Malaga car hire</li><li>Manchester hotels</li><li>Marrakech holidays</li></ul>
  <ul class="abs col" style="left:980px"><li>Mexico holidays</li><li>New York flights</li><li>New York holidays</li><li>Orlando flights</li><li>Orlando holidays</li></ul>
</section>

<footer class="abs footer">
  <div class="abs brand"><i></i>Rovanix</div>
  <div class="abs finfo">
    <div><svg width="12" height="16" viewBox="0 0 12 16"><path d="M6 0a6 6 0 00-6 6c0 4.5 6 10 6 10s6-5.5 6-10a6 6 0 00-6-6zm0 8.5A2.5 2.5 0 116 3.5a2.5 2.5 0 010 5z" fill="#ddd"/></svg><span>48 Harbor Lane, Milford, NC,<br>27500</span></div>
    <div><svg width="13" height="13" viewBox="0 0 24 24"><path fill="#ddd" d="M6.6 10.8a15 15 0 006.6 6.6l2.2-2.2c.3-.3.7-.4 1-.2 1.1.4 2.3.6 3.6.6.6 0 1 .4 1 1V20c0 .6-.4 1-1 1A17 17 0 013 4c0-.6.4-1 1-1h3.5c.6 0 1 .4 1 1 0 1.3.2 2.5.6 3.6.1.3 0 .7-.2 1z"/></svg><span>Phone:&nbsp; 1-800-555-0142</span></div>
    <div><svg width="13" height="11" viewBox="0 0 24 18"><rect x="1" y="1" width="22" height="16" fill="none" stroke="#ddd" stroke-width="2"/><path d="M1 1l11 9 11-9" fill="none" stroke="#ddd" stroke-width="2"/></svg><span>Email: info@rovanix.com</span></div>
  </div>
  <div class="abs fcol" style="left:358px"><h5>Asia</h5><ul><li>Bali</li><li>China</li><li>Hong Kong</li><li>Singapore</li><li>India</li><li>Malaysia</li></ul></div>
  <div class="abs fcol" style="left:522px"><h5>Indian Ocean</h5><ul><li>Maldives</li><li>Mauritius</li><li>Seychelles</li><li>Sri Lanka</li></ul></div>
  <div class="abs fcol" style="left:710px"><h5>Africa</h5><ul><li>Kenya</li><li>Tanzania</li><li>Zanzibar</li><li>South Africa</li></ul></div>
  <div class="abs news">
    <h5>Sign up for newsletter</h5>
    <p>Get exclusive deals and the latest news direct to your inbox, sign up today!</p>
    <div class="input">Enter Email</div>
    <div class="btn">Subscribe</div>
  </div>
</footer>
<div class="abs bottom">
  <span class="abs copy">© 2017 Rovanix. All Rights Reserved.</span>
  <div class="abs links"><span>About Us</span><span>Contact Us</span><span>Terms and Conditions</span><span>Privacy Policy</span><span>FAQ</span></div>
</div>

</body>
</html>
```